Business Card

THIS IS THE CARD INFORMATION
DEVELOPMENT I FINANCING I PROPERTY MANAGEMENT
DANIEL OKAFOR
3182 SW 74th Terrace
Cedar Grove, FL 33419
Telephone I 855.437.2618
Facsimile I 855.437.2675
Industry/Entity Type
Business

```html
<!DOCTYPE html>
<html lang="en">
<head>
<meta charset="utf-8">
<title>Rivas Montero &amp; Company – Business Card</title>
<link href="https://fonts.googleapis.com/css2?family=Montserrat:wght@700&family=Mulish:wght@300;400&display=swap" rel="stylesheet">
<style>
  :root {
    --plum: #4a0f40;
    --white: #ffffff;
    --backdrop: #b7b8ba;
    --backdrop-light: #c4c5c7;
  }
  * { margin: 0; padding: 0; box-sizing: border-box; }
  html, body { width: 1200px; height: 1000px; overflow: hidden; }
  body {
    background: radial-gradient(circle at 50% 50%, var(--backdrop-light) 0%, var(--backdrop) 70%);
    font-family: "Mulish", sans-serif;
    position: relative;
  }
  .card {
    position: absolute;
    left: 366px; top: 82px;
    width: 520px; height: 815px;
    background: var(--white);
    overflow: hidden;
  }
  .card__top {
    position: absolute; left: 0; top: 0;
    width: 100%; height: 608px;
    background: var(--plum);
  }
  .brand {
    position: absolute; left: 42px; top: 52px;
    display: flex; align-items: center; gap: 12px;
    color: var(--white);
  }
  .brand__dot {
    width: 80px; height: 80px; border-radius: 50%;
    background: var(--white); flex: none;
  }
  .brand__name {
    font-family: "Montserrat", sans-serif;
    font-weight: 700;
    font-size: 38px; line-height: 1;
    letter-spacing: -0.3px;
    display: flex; flex-direction: column;
  }
  .brand__name small {
    font-size: 20px; align-self: flex-end; margin-top: 4px; letter-spacing: 0;
  }
  .tagline {
    position: absolute; left: 0; top: 155px; width: 100%;
    text-align: center; color: var(--white);
    font-size: 15.5px; letter-spacing: 0.3px;
  }
  .tagline .sep { font-weight: 300; font-size: 20px; margin: 0 2px; vertical-align: -2px; }
  .contact {
    position: absolute; left: 0; top: 248px; width: 100%;
    text-align: center; color: var(--white);
  }
  .contact__name { font-weight: 300; font-size: 35px; letter-spacing: 0.5px; line-height: 44px; }
  .contact__address { margin-top: 14px; font-size: 20px; line-height: 31px; }
  .contact__lines { margin-top: 22px; font-size: 20px; line-height: 28px; }
  .emblem { position: absolute; left: 136px; top: 490px; }
</style>
</head>
<body>
  <div class="card">
    <div class="card__top"></div>

    <div class="brand">
      <span class="brand__dot"></span>
      <div class="brand__name">RIVAS MONTERO<small>&amp; COMPANY</small></div>
    </div>

    <p class="tagline">DEVELOPMENT<span class="sep">/</span>FINANCING<span class="sep">/</span>PROPERTY MANAGEMENT</p>

    <div class="contact">
      <h1 class="contact__name">DANIEL OKAFOR</h1>
      <p class="contact__address">3182 SW 74th Terrace<br>Cedar Grove, FL 33419</p>
      <p class="contact__lines">Telephone : 855.437.2618<br>Facsimile : 855.437.2675</p>
    </div>

    <svg class="emblem" width="244" height="244" viewBox="0 0 244 244" aria-hidden="true">
      <defs>
        <clipPath id="upper-half"><rect x="0" y="0" width="244" height="118"/></clipPath>
        <clipPath id="lower-half"><rect x="0" y="118" width="244" height="126"/></clipPath>
      </defs>
      <circle cx="122" cy="122" r="121" fill="#ffffff" clip-path="url(#upper-half)"/>
      <circle cx="122" cy="122" r="121" fill="#4a0f40" clip-path="url(#lower-half)"/>
    </svg>
  </div>
</body>
</html>
```